Duct Manufacturing Company new to the industry needs business card and stationary design

we are sheet metal duct manufacturers looking for a business card design to fit my new business logo.
nothing to crazy that will date, but want it to stand out from the crowed.
I'm sure you guys will work it out.

Contact Information for Business Card

Glen Marsh
Director

Address
17 Dorwell St
Queanbeyan NSW 2620

0438 760 514

Sales@flowbend.com.au

Font styles to use
Other font styles liked:
• BankGothic md bt

Requirements
Nice to have
• Like the idea of corner rounded to match logo
• like to keep colours flowing
• font I like sharp square not rounded

```html
<!DOCTYPE html>
<html lang="en">
<head>
<meta charset="utf-8">
<title>Flowbend Industries – Business Card</title>
<link href="https://fonts.googleapis.com/css2?family=Lato:wght@400;700;900&display=swap" rel="stylesheet">
<style>
  :root{
    --backdrop:#8e8d8e;
    --brand-blue:#034c98;
    --paper:#efefef;
    --ink-dark:#1b1b1b;
    --rule:#8ea9cf;
    --web-grey:#9fb4d2;
    --white:#ffffff;
  }
  *{box-sizing:border-box;margin:0;padding:0}
  html,body{width:1200px;height:900px;overflow:hidden}
  body{background:var(--backdrop);font-family:"Lato",sans-serif;position:relative}

  .card{position:absolute;width:560px;height:320px;border-radius:22px;overflow:hidden;
        box-shadow:0 6px 14px rgba(0,0,0,.25)}

  /* Front */
  .card-front{left:60px;top:90px;background:var(--brand-blue)}
  .front-brand{position:absolute;left:0;right:0;top:105px;text-align:center;color:var(--white)}
  .front-brand .brand-name{font-weight:900;font-size:40px;letter-spacing:3px;line-height:1}
  .front-brand .brand-sub{font-weight:900;font-size:22px;letter-spacing:9px;margin-top:6px}
  .front-web{position:absolute;left:50px;right:50px;top:235px;display:flex;align-items:center;gap:14px;
             color:var(--web-grey);font-size:15px;letter-spacing:.5px}
  .front-web .rule{flex:1;height:1px;background:var(--rule)}

  /* Back */
  .card-back{left:580px;top:490px;background:var(--paper)}
  .back-band{position:absolute;inset:0}
  .back-brand{position:absolute;right:32px;top:28px;text-align:right;color:var(--brand-blue);display:flex;align-items:center;gap:10px}
  .back-brand .mark-dot{width:18px;height:18px;border-radius:50%;background:var(--brand-blue)}
  .back-brand .brand-name{font-weight:900;font-size:24px;letter-spacing:2px;line-height:1}
  .back-brand .brand-sub{font-weight:900;font-size:13px;letter-spacing:5px;margin-top:3px}
  .person{position:absolute;left:40px;top:118px}
  .person .name{font-weight:900;font-size:26px;color:var(--brand-blue);letter-spacing:-.3px}
  .person .role{font-size:15px;color:var(--ink-dark);margin-top:2px}
  .contact{position:absolute;right:30px;top:168px;text-align:right;color:var(--white);font-size:15px;line-height:21px}
  .contact li{list-style:none;display:flex;justify-content:flex-end;align-items:center;gap:8px}
  .contact svg{width:13px;height:13px;flex:none}
  .contact .gap{height:6px}
  .band-name{position:absolute;left:36px;bottom:40px;color:var(--white);font-weight:900;font-size:34px;letter-spacing:3px}
</style>
</head>
<body>

<section class="card card-front" aria-label="Card front">
  <div class="front-brand">
    <div class="brand-name">FLOWBEND</div>
    <div class="brand-sub">INDUSTRIES</div>
  </div>
  <div class="front-web">
    <span class="rule"></span>
    <span class="url">www.flowbend.com.au</span>
    <span class="rule"></span>
  </div>
</section>

<section class="card card-back" aria-label="Card back">
  <svg class="back-band" viewBox="0 0 560 320" preserveAspectRatio="none" aria-hidden="true">
    <polygon points="0,178 560,132 560,282 150,320 0,320" fill="var(--brand-blue)"/>
  </svg>

  <div class="back-brand">
    <span class="mark-dot"></span>
    <div>
      <div class="brand-name">FLOWBEND</div>
      <div class="brand-sub">INDUSTRIES</div>
    </div>
  </div>

  <div class="person">
    <div class="name">Glen Marsh</div>
    <div class="role">Director</div>
  </div>

  <ul class="contact">
    <li>17 Dorwell St</li>
    <li>Queanbeyan NSW 2620</li>
    <li class="gap"></li>
    <li>0438 760 514
      <svg viewBox="0 0 16 16"><path fill="#fff" d="M3 1l3 3-2 2c1 2 3 4 5 5l2-2 3 3-2 3C6 14 2 10 1 4z"/></svg></li>
    <li>Sales@flowbend.com.au
      <svg viewBox="0 0 16 16"><rect x="1" y="3" width="14" height="10" fill="none" stroke="#fff" stroke-width="1.6"/><path d="M1 3l7 6 7-6" fill="none" stroke="#fff" stroke-width="1.6"/></svg></li>
    <li>www.flowbend.com.au
      <svg viewBox="0 0 16 16"><rect x="1.5" y="2" width="13" height="9" fill="none" stroke="#fff" stroke-width="1.6"/><path d="M5 14h6M8 11v3" stroke="#fff" stroke-width="1.6"/></svg></li>
  </ul>

  <div class="band-name">FLOWBEND</div>
</section>

</body>
</html>
```